The most modern business card ever !!!

Our company call “Vendalo”. Vendalo is a technology company specialized in cruises solutions. Out main product is a platform to reserve cruises. This is a revolutionary platform that make easier to travel agencies and final users to reserve cruises across dozen companies like tibba, wernu, hpv, dgb, etc..We are a “start up”, with a young team of developers and we want to transmit it.. For it, we want something different, a modern business card that represent cruises and technology.. When someone receive this card, this person should say: wowww this is different… this is modern… this is a cruise related company..
- diferent, modern
- traditions business card

```html
<!DOCTYPE html>
<html lang="en">
<head>
<meta charset="utf-8">
<title>Vendalo business card</title>
<link rel="stylesheet" href="https://fonts.googleapis.com/css2?family=Tinos&display=swap">
<style>
  :root {
    --backdrop: #2a2a2b;
    --card: #1b1b1c;
    --text: #f2f2f2;
    --muted: #8c8c8e;
    --accent: #29a8e0;
    --rule: #d9d9d9;
  }
  * { box-sizing: border-box; margin: 0; padding: 0; }
  html, body { width: 1200px; height: 895px; overflow: hidden; }
  body {
    background: var(--backdrop);
    font-family: "Tinos", serif;
    display: flex;
    flex-direction: column;
    align-items: center;
    justify-content: center;
    gap: 40px;
  }
  .card {
    width: 630px;
    height: 360px;
    background: var(--card);
    position: relative;
    box-shadow: 0 14px 30px rgba(0,0,0,.45);
    display: flex;
    align-items: center;
  }
  .card--logo { justify-content: center; }
  .card--logo .brand-name {
    font-size: 84px;
    color: var(--muted);
    letter-spacing: 2px;
  }
  .card--contact {
    justify-content: center;
    gap: 28px;
    border-bottom: 6px solid var(--accent);
  }
  .card--contact .brand-name {
    font-size: 52px;
    color: var(--text);
    letter-spacing: 1px;
  }
  .divider {
    width: 2px;
    height: 92px;
    background: var(--rule);
  }
  .contact-list { list-style: none; display: flex; flex-direction: column; gap: 8px; }
  .contact-item {
    display: flex;
    align-items: center;
    gap: 12px;
    color: var(--text);
    font-size: 18px;
  }
  .contact-icon { width: 16px; height: 16px; flex: none; }
  .contact-icon * { fill: none; stroke: var(--accent); stroke-width: 1.6; }
</style>
</head>
<body>
  <section class="card card--logo">
    <span class="brand-name">Vendalo</span>
  </section>

  <section class="card card--contact">
    <span class="brand-name">Vendalo</span>
    <span class="divider"></span>
    <ul class="contact-list">
      <li class="contact-item">
        <svg class="contact-icon" viewBox="0 0 16 16"><rect x="4" y="1.5" width="8" height="13" rx="1.5"/><line x1="7" y1="12" x2="9" y2="12"/></svg>
        000 000 0000
      </li>
      <li class="contact-item">
        <svg class="contact-icon" viewBox="0 0 16 16"><rect x="1.5" y="3.5" width="13" height="9"/><polyline points="1.5,3.5 8,9 14.5,3.5"/></svg>
        info@vendalo.com
      </li>
      <li class="contact-item">
        <svg class="contact-icon" viewBox="0 0 16 16"><circle cx="8.5" cy="7" r="5"/><line x1="5" y1="10.5" x2="2" y2="14"/></svg>
        www.vendalo.com
      </li>
    </ul>
  </section>
</body>
</html>
```